Direct to Consumer extended service contract business with a new disruptive business model needs a

We need a customized wordpress design for a company called 'Bright Harbor Assurance'.
We provide an innovative and unique service contract protection program direct to consumers. This program provides monthly coverage for all electronics purchased in the last 4 years and all electronics the consumer purchases in the future for a low monthly fee. The overall design should communicate a sense of legitimacy, ethics, and superior customer service and support (in an industry that has a huge PR issue to overcome).
Electronics is the first product group, other product groups with different price points to launch in the future..

Target Market(s)

All purchasers of electronic goods...all demographics

Industry/Entity Type

Electronics

Font styles to use
Sans Serif

Requirements
Must have
• Customer Testimonials
Industry News
Customer ratings
Blog posts
Call to action messaging
Like the functional elements and design of quillmesa.example (need to be better)
Nice to have
• Like to see video testimonials
Social network "whats trending related to electronics or service contract industry"
Easy way to register products for warranty

```html
<!DOCTYPE html>
<html lang="en">
<head>
<meta charset="utf-8">
<title>Bright Harbor Assurance</title>
<link rel="stylesheet" href="https://fonts.googleapis.com/css2?family=Open+Sans:ital,wght@0,300;0,400;0,600;0,700;1,400&display=swap">
<style>
:root{
  --green:#2b9a3e;
  --green-dark:#23832f;
  --ink:#333;
  --muted:#777;
  --band:#3a3a3a;
  --band-deep:#2d2d2d;
  --news:#1f1f1f;
  --line:#e2e2e2;
  --white:#fff;
  --star:#f1b91f;
}
*{box-sizing:border-box;margin:0;padding:0}
html,body{width:1200px;height:2359px;overflow:hidden}
body{position:relative;background:var(--white);font-family:"Open Sans",Arial,sans-serif;color:var(--ink)}
.abs{position:absolute}
.ph{position:absolute;display:block}

/* header */
.site-header{position:absolute;left:0;top:0;width:1200px;height:79px;border-bottom:1px solid var(--line)}
.brand{left:171px;top:20px;font-size:22px;font-weight:700;color:var(--green);letter-spacing:.5px}
.util{top:33px;font-size:12px;color:#555}
.util-sep{left:768px;top:32px;font-size:12px;color:#aaa}
.call-icon{left:846px;top:22px}
.call-label{left:896px;top:24px;font-size:12px;color:#555}
.call-number{left:896px;top:43px;font-size:13px;color:var(--green)}

/* nav */
.main-nav{position:absolute;left:171px;top:110px;width:858px;height:57px;display:flex}
.nav-item{flex:1;background:var(--green);color:var(--white);padding:13px 0 0 20px;border-left:1px solid rgba(255,255,255,.35)}
.nav-item:first-child{background:#6b6b6b;border-left:none}
.nav-item b{display:block;font-size:12px;font-weight:600}
.nav-item span{display:block;font-size:11px;margin-top:3px}

/* hero */
.hero{position:absolute;left:171px;top:167px;width:858px;height:358px;background:linear-gradient(#fafafa,#e9e9e9)}
.hero-title{left:49px;top:64px;font-size:31px;font-weight:300;color:#333}
.hero-sub{left:49px;top:108px;font-size:18px;font-weight:300;color:#666;line-height:27px;width:300px}
.hero-btn{left:51px;top:179px;width:311px;height:44px;background:#666;border-radius:3px;color:#eee;font-size:14px;line-height:44px;text-align:center;box-shadow:0 2px 3px rgba(0,0,0,.25)}
.hero-brand{left:49px;top:243px;font-size:18px;font-weight:700;color:var(--green);white-space:nowrap}
.hero-tag{left:49px;top:275px;font-size:12px;color:#555}
.hero-device{left:392px;top:48px;width:445px;height:257px;border-radius:10px 10px 4px 4px;background:linear-gradient(#dcdcdc,#f3f3f3 60%,#bdbdbd)}
.dots{left:579px;top:319px;display:flex;gap:5px}
.dots i{width:10px;height:10px;border-radius:50%;background:#aaa;display:block}
.dots i:first-child{background:var(--green)}

/* ratings */
.ratings{position:absolute;left:0;top:547px;width:1200px;height:194px;background:var(--band)}
.ratings-title{width:1200px;top:26px;text-align:center;color:#e6e6e6;font-size:17px;font-weight:300}
.store-mark{width:60px;height:60px;border-radius:8px;background:#5b5b5b}
.store-name{font-size:18px;color:#eee;font-weight:300}
.store-note{font-size:11px;color:#ccc}
.store-word{font-size:24px;color:#fff;font-weight:300}

/* features */
.feat-icon{width:66px;height:66px;border-radius:50%}
.feat-kicker{font-size:19px;font-weight:300;color:#555}
.feat-title{font-size:23px;font-weight:300;color:#333}
.feat-list{list-style:none;font-size:11.5px;color:#555}
.feat-list li{height:23px;display:flex;align-items:center;gap:8px}

/* testimonial */
.video{left:171px;top:991px;width:326px;height:208px;background:linear-gradient(135deg,#8a8a8a,#2c2c2c)}
.video-bar{left:177px;top:1170px;width:314px;height:22px;background:rgba(40,40,40,.85);border-radius:3px}
.section-title{font-size:23px;font-weight:300;color:#333}
.pager{font-size:14px;color:#666;letter-spacing:4px}
.quote-text{left:576px;top:1048px;width:395px;font-size:10.5px;font-style:italic;line-height:20px;color:#444}
.quote-mark{font-size:40px;color:#999;font-family:Georgia,serif}
.quote-name{left:576px;top:1160px;font-size:13px;color:var(--green)}
.quote-role{left:576px;top:1180px;font-size:11px;color:#666}

/* news */
.news{position:absolute;left:0;top:1268px;width:1200px;height:436px;background:linear-gradient(180deg,#1b1b1b,#2c2c2c 50%,#1d1d1d)}
.card-img{width:254px;height:139px}
.card-title{font-size:15px;font-weight:300}
.card-date{font-size:11px;font-style:italic}
.card-rule{width:254px;height:1px;background:#555}
.card-text{width:250px;font-size:11px;line-height:21px;color:#ddd}

/* footer */
.footer{position:absolute;left:0;top:2092px;width:1200px;height:223px;background:#3d3d3d;color:#ddd}
.foot-bottom{position:absolute;left:0;top:2315px;width:1200px;height:44px;background:#2c2c2c;color:#bbb;font-size:11px;text-align:center;line-height:44px}
.foot-social{left:173px;top:33px;font-size:26px;font-weight:700;color:#fff}
.foot-head{font-size:15px;color:#fff}
.foot-links{list-style:none;font-size:11px;color:#ccc}
.foot-links li{height:23px}
.email-field{left:749px;top:91px;width:250px;height:29px;background:#fff;border-radius:3px;color:#555;font-size:11px;line-height:29px;padding-left:12px}
.subscribe{left:749px;top:131px;width:250px;height:31px;background:var(--green);border-radius:2px;color:#fff;font-size:12px;font-weight:600;text-align:center;line-height:31px}
</style>
</head>
<body>

<header class="site-header">
  <div class="abs brand">Bright Harbor Assurance</div>
  <div class="abs util" style="left:725px">Login</div>
  <div class="abs util-sep">|</div>
  <div class="abs util" style="left:783px">Support</div>
  <svg class="abs call-icon" width="40" height="40" viewBox="0 0 40 40" aria-hidden="true">
    <circle cx="20" cy="20" r="18" fill="none" stroke="#999" stroke-width="1.5"/>
    <path d="M13 12c2-2 4 2 5 4 1 1-1 2-1 3 1 2 3 4 5 5 1 0 2-2 3-1 2 1 6 3 4 5-2 3-6 3-10 0-3-2-6-5-7-9-1-3 0-5 1-7z" fill="#888"/>
  </svg>
  <div class="abs call-label">Call Us :</div>
  <div class="abs call-number">855-555-BRIGHT (274448)</div>
</header>

<nav class="main-nav">
  <div class="nav-item"><b>HOME</b><span>Welcome to Bright Harbor</span></div>
  <div class="nav-item"><b>PLANS</b><span>Visit our Plans</span></div>
  <div class="nav-item"><b>BENEFITS</b><span>Get our Product benefits</span></div>
  <div class="nav-item"><b>FAQ'S</b><span>Ask your Questions</span></div>
  <div class="nav-item"><b>ABOUT US</b><span>Know about our History</span></div>
</nav>

<section class="hero">
  <h1 class="abs hero-title" style="font-weight:300">The Days of Buying</h1>
  <p class="abs hero-sub">Expensive in-Store Service plans are Over!</p>
  <div class="abs hero-btn">Don't buy anymore in-store service plans</div>
  <div class="abs hero-brand">BRIGHT HARBOR ASSURANCE</div>
  <div class="abs hero-tag">IS THE SOLUTION</div>
  <div class="ph hero-device" role="img" aria-label="Laptop showing the Bright Harbor Assurance website"></div>
  <div class="abs dots"><i></i><i></i><i></i></div>
</section>

<section class="ratings">
  <h2 class="abs ratings-title" style="font-weight:300">Rated #1 by the people who matter most: our customers.</h2>

  <div class="abs store-mark" style="left:180px;top:68px"></div>
  <div class="abs store-word" style="left:171px;top:132px">Orchard</div>
  <svg class="abs" style="left:277px;top:86px" width="94" height="18" aria-hidden="true"><g id="stars">
    <path d="M9 1l2.4 5 5.4.6-4 3.7 1.1 5.4L9 13l-4.9 2.7 1.1-5.4-4-3.7 5.4-.6z" fill="var(--star)"/>
    <path transform="translate(23 0)" d="M9 1l2.4 5 5.4.6-4 3.7 1.1 5.4L9 13l-4.9 2.7 1.1-5.4-4-3.7 5.4-.6z" fill="var(--star)"/>
    <path transform="translate(46 0)" d="M9 1l2.4 5 5.4.6-4 3.7 1.1 5.4L9 13l-4.9 2.7 1.1-5.4-4-3.7 5.4-.6z" fill="var(--star)"/>
    <path transform="translate(69 0)" d="M9 1l2.4 5 5.4.6-4 3.7 1.1 5.4L9 13l-4.9 2.7 1.1-5.4-4-3.7 5.4-.6z" fill="#999"/></g></svg>
  <div class="abs store-name" style="left:277px;top:114px">Orchard App Shop</div>
  <div class="abs store-note" style="left:277px;top:142px">4.5 average on 7000+ reviews</div>

  <div class="abs store-mark" style="left:499px;top:82px;width:70px;height:70px"></div>
  <svg class="abs" style="left:597px;top:82px" width="94" height="18" aria-hidden="true"><use href="#stars"/></svg>
  <div class="abs store-name" style="left:597px;top:110px">Orchard App Shop</div>
  <div class="abs store-note" style="left:597px;top:138px">4.5 average on 7000+ reviews</div>

  <div class="abs store-mark" style="left:787px;top:82px;width:70px;height:70px"></div>
  <svg class="abs" style="left:880px;top:82px" width="94" height="18" aria-hidden="true"><use href="#stars"/></svg>
  <div class="abs store-name" style="left:880px;top:110px">Orchard App Shop</div>
  <div class="abs store-note" style="left:880px;top:138px">4.5 average on 7000+ reviews</div>
</section>

<svg width="0" height="0" style="position:absolute" aria-hidden="true">
  <symbol id="tick" viewBox="0 0 12 10"><path d="M1 5l3.5 3.5L11 1" fill="none" stroke="#7cb342" stroke-width="2"/></symbol>
</svg>

<section class="features">
  <div class="ph feat-icon" style="left:171px;top:794px;background:radial-gradient(circle at 35% 35%,#eee,#888)" role="img" aria-label="Globe icon"></div>
  <div class="abs feat-kicker" style="left:256px;top:797px">Superior</div>
  <div class="abs feat-title" style="left:256px;top:820px">Coverage</div>
  <ul class="abs feat-list" style="left:250px;top:857px">
    <li><svg width="12" height="10"><use href="#tick"/></svg>One plan covers all electronic products</li>
    <li><svg width="12" height="10"><use href="#tick"/></svg>Thousands of Eligible products</li>
    <li><svg width="12" height="10"><use href="#tick"/></svg>Register any brand from any retailer</li>
  </ul>

  <svg class="abs" style="left:480px;top:796px" width="66" height="74" viewBox="0 0 66 74" role="img" aria-label="Shield with tick">
    <path d="M33 2l28 10v20c0 20-13 33-28 40C18 65 5 52 5 32V12z" fill="#2e9e3a" stroke="#bbb" stroke-width="3"/>
    <path d="M19 37l10 10 19-22" fill="none" stroke="#fff" stroke-width="6"/>
  </svg>
  <div class="abs feat-kicker" style="left:565px;top:797px">Revolutionary</div>
  <div class="abs feat-title" style="left:565px;top:820px">Protection</div>
  <ul class="abs feat-list" style="left:557px;top:857px">
    <li><svg width="12" height="10"><use href="#tick"/></svg>Repair, Replace or Refund</li>
    <li><svg width="12" height="10"><use href="#tick"/></svg>Cover past, present and future purchases</li>
    <li><svg width="12" height="10"><use href="#tick"/></svg>Coverage never ends</li>
  </ul>

  <div class="ph feat-icon" style="left:802px;top:796px;border-radius:8px;background:linear-gradient(#ddd,#777)" role="img" aria-label="Headset icon"></div>
  <div class="abs feat-kicker" style="left:881px;top:797px">Hassle Free</div>
  <div class="abs feat-title" style="left:881px;top:823px;font-size:19px">Customer service</div>
  <ul class="abs feat-list" style="left:876px;top:857px">
    <li><svg width="12" height="10"><use href="#tick"/></svg>24 hr. customer Hotline</li>
    <li><svg width="12" height="10"><use href="#tick"/></svg>Over 10,000 service centers</li>
    <li><svg width="12" height="10"><use href="#tick"/></svg>No questions asked</li>
  </ul>
</section>

<section class="testimonials">
  <div class="ph video" role="img" aria-label="Video testimonial from a customer"></div>
  <svg class="abs" style="left:306px;top:1063px" width="64" height="64" aria-hidden="true">
    <circle cx="32" cy="32" r="30" fill="rgba(255,255,255,.35)"/><path d="M25 19l22 13-22 13z" fill="#fff"/>
  </svg>
  <div class="abs video-bar"></div>
  <svg class="abs" style="left:181px;top:1173px" width="30" height="16" aria-hidden="true"><rect width="30" height="16" rx="2" fill="#555"/><path d="M12 4l8 4-8 4z" fill="#fff"/></svg>
  <div class="abs" style="left:220px;top:1181px;width:180px;height:3px;background:#777"></div>
  <div class="abs" style="left:440px;top:1175px;font-size:10px;color:#ddd">Reelbox</div>

  <h2 class="abs section-title" style="left:547px;top:993px">Customer Testimonials</h2>
  <div class="abs pager" style="left:933px;top:997px">‹ ›</div>
  <div class="abs quote-mark" style="left:550px;top:1033px">“</div>
  <p class="abs quote-text">The days of costly, store-bought extended warranties are coming to an end. Bright Harbor Assurance is revolutionizing the extended service and repair industry! Traditional service plans purchased at big box electronic stores or online require you to pay large upfront premiums for each consumer electronics device protected.</p>
  <div class="abs quote-mark" style="left:980px;top:1108px">”</div>
  <div class="abs quote-name">Dorian Pell</div>
  <div class="abs quote-role">Marketing Executive</div>
</section>

<section class="news" aria-label="Industry News">
  <h2 class="abs section-title" style="width:1200px;top:56px;text-align:center;color:#fff">Industry News</h2>
  <div class="abs pager" style="left:1004px;top:62px;color:#ccc">‹ ›</div>

  <div class="ph card-img" style="left:171px;top:127px;background:linear-gradient(135deg,#eee,#888)" role="img" aria-label="Person walking through an abstract grey space"></div>
  <div class="abs card-title" style="left:171px;top:280px;color:#fff">A Revolutionary Protection</div>
  <div class="abs card-date" style="left:171px;top:306px;color:#fff">Posted on 27 march 2014</div>
  <div class="abs card-rule" style="left:171px;top:330px"></div>
  <p class="abs card-text" style="left:171px;top:340px">The days of costly, store-bought extended warranties are coming to an end.</p>

  <div class="ph card-img" style="left:472px;top:127px;background:linear-gradient(135deg,#0d4f86,#35a2d8)" role="img" aria-label="Woman using a futuristic touch interface"></div>
  <div class="abs card-title" style="left:472px;top:280px;color:#fff">A Revolutionary Protection</div>
  <div class="abs card-date" style="left:472px;top:306px;color:#fff">Posted on 27 march 2014</div>
  <div class="abs card-rule" style="left:472px;top:330px"></div>
  <p class="abs card-text" style="left:472px;top:340px">The days of costly, store-bought extended warranties are coming to an end.</p>

  <div class="ph card-img" style="left:775px;top:127px;background:linear-gradient(135deg,#3a2a1c,#c49a74)" role="img" aria-label="Woman holding a light bulb"></div>
  <div class="abs card-title" style="left:775px;top:280px;color:#fff">A Revolutionary Protection</div>
  <div class="abs card-date" style="left:775px;top:306px;color:#fff">Posted on 27 march 2014</div>
  <div class="abs card-rule" style="left:775px;top:330px"></div>
  <p class="abs card-text" style="left:775px;top:340px">The days of costly, store-bought extended warranties are coming to an end.</p>
</section>

<section class="blog" aria-label="Blog posts">
  <h2 class="abs section-title" style="width:1200px;top:1746px;text-align:center">Blog posts</h2>
  <div class="abs pager" style="left:1004px;top:1751px">‹ ›</div>

  <div class="ph" style="left:171px;top:1803px;width:254px;height:190px;background:linear-gradient(135deg,#1a1a1a,#b07a3c)" role="img" aria-label="Hand holding a tablet with floating app icons"></div>
  <div class="abs card-title" style="left:171px;top:2006px">A Revolutionary Protection</div>
  <div class="abs card-date" style="left:171px;top:2032px;color:#555">Posted on 27 march 2014</div>

  <div class="ph" style="left:472px;top:1803px;width:254px;height:190px;background:linear-gradient(135deg,#7da6c6,#4b3e35)" role="img" aria-label="Businessman looking through binoculars"></div>
  <div class="abs card-title" style="left:472px;top:2006px">A Revolutionary Protection</div>
  <div class="abs card-date" style="left:472px;top:2032px;color:#555">Posted on 27 march 2014</div>

  <div class="ph" style="left:775px;top:1803px;width:254px;height:190px;background:linear-gradient(135deg,#f2f5f8,#9aa8b5)" role="img" aria-label="Two business people shaking hands in a bright office"></div>
  <div class="abs card-title" style="left:775px;top:2006px">A Revolutionary Protection</div>
  <div class="abs card-date" style="left:775px;top:2032px;color:#555">Posted on 27 march 2014</div>
</section>

<footer class="footer">
  <div class="abs foot-social">Socialnest</div>
  <div class="abs pager" style="left:374px;top:40px;color:#bbb">‹ ›</div>
  <div class="abs" style="left:173px;top:83px;font-size:11px;font-weight:600;color:#fff">The days of costly, store-bought</div>
  <p class="abs" style="left:173px;top:108px;width:260px;font-size:10.5px;line-height:19px;color:#ccc">The days of costly, store-bought extended warranties are coming to an end. Bright Harbor Assurance is revolutionizing the extended service...</p>
  <div class="abs" style="left:173px;top:170px;font-size:10.5px;color:#bbb;text-decoration:underline">www.quillmesa.example</div>

  <div class="abs foot-head" style="left:483px;top:33px">Welcome</div>
  <ul class="abs foot-links" style="left:483px;top:67px"><li>Plans</li><li>Benefits</li><li>FAQs</li><li>About Us</li></ul>
  <ul class="abs foot-links" style="left:577px;top:67px"><li>Support</li><li>Privacy Policy</li><li>Terms &amp; Conditions</li><li>Contact Us</li></ul>

  <div class="abs foot-head" style="left:749px;top:33px;width:220px;line-height:23px">Get Your Bright Harbor Assurance Today!</div>
  <div class="abs email-field">Enter your email id :</div>
  <div class="abs subscribe">SUBSCRIBE NOW</div>
</footer>
<div class="foot-bottom">© 2014 Bright Harbor Assurance. All Rights Reserved.</div>

</body>
</html>
```